Business card design for my company.
I would like the card's background colour to be black. You can also see our web site to get an idea of our brand. https://www.tmwhomecrafting.com.au/
- Name
- Email

```html
<!DOCTYPE html>
<html lang="en">
<head>
<meta charset="utf-8">
<title>TMW Home Crafting — Business Card</title>
<link href="https://fonts.googleapis.com/css2?family=Montserrat:wght@400;500;700&display=swap" rel="stylesheet">
<style>
  :root {
    --stage: #c4c4c4;
    --card: #222222;
    --green: #16973f;
    --white: #f4f5f7;
    --muted: #d9d9d9;
  }
  * { box-sizing: border-box; margin: 0; padding: 0; }
  html, body {
    width: 1200px; height: 802px; overflow: hidden;
    background: var(--stage);
    font-family: "Montserrat", sans-serif;
  }
  .stage {
    width: 1200px; height: 802px;
    display: flex; align-items: center; justify-content: center; gap: 40px;
  }
  .card {
    position: relative;
    width: 540px; height: 310px;
    background: var(--card);
    border-radius: 18px;
    overflow: hidden;
  }
  .card--front { border-bottom: 7px solid var(--green); }

  .brand {
    position: absolute;
    display: flex; align-items: center; gap: 10px;
    color: var(--white);
    font-weight: 700;
    letter-spacing: 0.06em;
    text-transform: uppercase;
  }
  .brand__mark { width: 14px; height: 14px; background: var(--green); flex: none; }
  .brand__name { line-height: 1.25; }

  .card--front .brand {
    left: 40px; top: 50%; transform: translateY(-50%);
    width: 190px; font-size: 18px;
  }
  .card--front .brand__mark { width: 16px; height: 16px; }
  .card--back .brand {
    left: 50%; top: 50%; transform: translate(-50%, -50%);
    font-size: 30px; gap: 16px; white-space: nowrap;
  }
  .card--back .brand__mark { width: 24px; height: 24px; }

  .divider {
    position: absolute; left: 262px; top: 68px;
    width: 1px; height: 170px; background: var(--green);
  }
  .details { position: absolute; left: 286px; top: 74px; }
  .details__name {
    color: var(--green); font-weight: 700; font-size: 19px;
    letter-spacing: 0.04em; text-transform: uppercase;
  }
  .details__role { color: var(--muted); font-size: 13px; margin-top: 2px; }
  .contact { list-style: none; margin-top: 26px; }
  .contact__item {
    display: flex; align-items: center; gap: 8px;
    color: var(--muted); font-size: 12px; line-height: 1; margin-bottom: 11px;
    white-space: nowrap;
  }
  .contact__icon { width: 11px; height: 11px; flex: none; fill: var(--green); }
</style>
</head>
<body>
<main class="stage">
  <section class="card card--front" aria-label="Business card front">
    <div class="brand"><span class="brand__mark"></span><span class="brand__name">TMW Home Crafting</span></div>
    <div class="divider"></div>
    <div class="details">
      <p class="details__name">Dale Harper</p>
      <p class="details__role">CEO/Founder</p>
      <ul class="contact">
        <li class="contact__item">
          <svg class="contact__icon" viewBox="0 0 24 24" aria-hidden="true"><path d="M6.6 10.8a15 15 0 0 0 6.6 6.6l2.2-2.2a1 1 0 0 1 1-.25 11.4 11.4 0 0 0 3.6.57 1 1 0 0 1 1 1V20a1 1 0 0 1-1 1A17 17 0 0 1 3 4a1 1 0 0 1 1-1h3.5a1 1 0 0 1 1 1c0 1.25.2 2.45.57 3.57a1 1 0 0 1-.25 1z"/></svg>
          555-214-7390
        </li>
        <li class="contact__item">
          <svg class="contact__icon" viewBox="0 0 24 24" aria-hidden="true"><path d="M2 5h20v14H2z"/><path d="M2 5l10 8 10-8" fill="none" stroke="#222" stroke-width="2"/></svg>
          info@tmwhomecrafting.com.au
        </li>
        <li class="contact__item">
          <svg class="contact__icon" viewBox="0 0 24 24" aria-hidden="true"><circle cx="12" cy="12" r="10"/></svg>
          www.tmwhomecrafting.com.au
        </li>
      </ul>
    </div>
  </section>

  <section class="card card--back" aria-label="Business card back">
    <div class="brand"><span class="brand__mark"></span><span class="brand__name">TMW Home Crafting</span></div>
  </section>
</main>
</body>
</html>
```